Brightmill Data Works

Our company is about IT hardwares and IT solutions. IT hardware such as PC, RAMS, storage and servers. IT solutions such as project management, BA. We are also selling new technology too.

Target Market(s)

Consumer, Small to Medium Business, Corporate

Requirements
Must have
• The business card must have the following:
• Name:
• Title:
• Contact Number:
• Email address:
• Website:
• Color: Must match the logo color upgrade

```html
<!DOCTYPE html>
<html lang="en">
<head>
<meta charset="utf-8">
<title>Brightmill Data Works – Business Card</title>
<link href="https://fonts.googleapis.com/css2?family=Saira:wght@300;400;700&display=swap" rel="stylesheet">
<style>
  :root {
    --backdrop: #2a2a2a;
    --card: #f1f1f1;
    --ink: #3a3a3a;
    --copper: #c9782c;
    --copper-light: #d08a36;
    --copper-deep: #bb6a27;
  }
  * { box-sizing: border-box; margin: 0; padding: 0; }
  html, body {
    width: 1200px; height: 923px; overflow: hidden;
    background: var(--backdrop);
    font-family: "Saira", sans-serif;
  }
  .canvas {
    position: relative; width: 1200px; height: 923px;
    display: flex; align-items: center; justify-content: center;
  }
  .card {
    position: relative; width: 1000px; height: 572px;
    background: var(--card);
    overflow: hidden;
  }
  .card__band {
    position: absolute; left: 0; top: 0; bottom: 0; width: 172px;
    background: linear-gradient(90deg, var(--copper-light), var(--copper-deep));
  }
  .card__info {
    position: absolute; right: 56px; top: 48px;
    display: flex; flex-direction: column; align-items: flex-end;
    text-align: right;
  }
  .brand {
    display: flex; flex-direction: column; align-items: flex-end;
  }
  .brand__mark {
    width: 42px; height: 42px; background: var(--copper);
    margin-bottom: 14px;
  }
  .brand__name {
    font-weight: 700; color: var(--ink);
    font-size: 40px; line-height: 1.0; letter-spacing: 0.5px;
    text-transform: uppercase;
  }
  .person { margin-top: 34px; }
  .person__name {
    font-weight: 400; font-size: 30px; color: var(--ink);
    text-transform: uppercase; line-height: 1.1;
  }
  .person__title {
    font-weight: 400; font-size: 20px; color: var(--copper);
    text-transform: uppercase; letter-spacing: 0.5px;
  }
  .contacts { margin-top: 30px; list-style: none; }
  .contacts__item {
    display: flex; align-items: center; justify-content: flex-end;
    gap: 12px; font-size: 24px; font-weight: 400; color: var(--ink);
    line-height: 1.4;
  }
  .contacts__icon {
    width: 22px; height: 22px; background: var(--copper);
    border-radius: 2px; display: flex; align-items: center; justify-content: center;
  }
  .contacts__icon svg { width: 15px; height: 15px; }
</style>
</head>
<body>
<main class="canvas">
  <section class="card" aria-label="Business card, front">
    <div class="card__band"></div>

    <div class="card__info">
      <div class="brand">
        <div class="brand__mark"></div>
        <div class="brand__name">Brightmill Data<br>Works</div>
      </div>

      <div class="person">
        <div class="person__name">Aaron Vale</div>
        <div class="person__title">Manager</div>
      </div>

      <ul class="contacts">
        <li class="contacts__item">+1-555-014-2290
          <span class="contacts__icon">
            <svg viewBox="0 0 16 16"><path fill="#fff" d="M4 1.5l2 3-1.3 1.3c.7 1.7 2 3 3.7 3.7L9.7 8.2l3 2-1 2.8C6.8 13 3 9.2 3 4.3z"/></svg>
          </span>
        </li>
        <li class="contacts__item">aaron@brightmill.com
          <span class="contacts__icon">
            <svg viewBox="0 0 16 16"><rect x="2" y="4" width="12" height="8" fill="none" stroke="#fff" stroke-width="1.4"/><path d="M2 4l6 5 6-5" fill="none" stroke="#fff" stroke-width="1.4"/></svg>
          </span>
        </li>
        <li class="contacts__item">www.brightmill.com
          <span class="contacts__icon">
            <svg viewBox="0 0 16 16" fill="none" stroke="#fff" stroke-width="1.2"><circle cx="8" cy="8" r="6"/><ellipse cx="8" cy="8" rx="2.6" ry="6"/><path d="M2 8h12"/></svg>
          </span>
        </li>
      </ul>
    </div>
  </section>
</main>
</body>
</html>
```